Veltrano.co - Polar Expeditions Specialists

We need a modern, visually striking business card for Veltrano.co, a company specialized in selling expedition cruises to the most remote regions on Earth, with a focus on the Arctic and Antarctica. The design should instantly communicate that the cardholder is an expert in polar travel. Use clean, premium aesthetics with cool tones like icy blue and white, possibly incorporating polar imagery (ice, glaciers, penguins, etc.)

Attached the logo

Contact Information for Business Card

Feels high-end and trustworthy.. Visually memorable — encourages people to keep it

Colors
0054AA
0677BA
7BADD7
CADEEF
E8F1F8

Requirements
Must have
• ice, glaciers, penguins, montains
Nice to have
• modern, transparente,

```html
<!DOCTYPE html>
<html lang="en">
<head>
<meta charset="utf-8">
<title>Veltrano.co – Business Card</title>
<link href="https://fonts.googleapis.com/css2?family=Poppins:wght@500;700&family=Arimo:wght@400;700&display=swap" rel="stylesheet">
<style>
  :root {
    --stage: #9b9b9b;
    --paper: #f4f4f3;
    --brand-blue: #2f6faf;
    --accent-blue: #3b7cc2;
    --ink: #2b2b2b;
    --rule: #6a6a6a;
    --white: #ffffff;
  }
  * { box-sizing: border-box; margin: 0; padding: 0; }
  html, body { width: 1200px; height: 1050px; overflow: hidden; }
  body {
    position: relative;
    background: var(--stage);
    font-family: "Arimo", Arial, sans-serif;
  }
  .card {
    position: absolute;
    border-radius: 22px;
    overflow: hidden;
  }
  /* Front: portrait */
  .card-front {
    left: 80px; top: 210px;
    width: 360px; height: 630px;
    background: var(--paper);
  }
  .front-brand {
    position: absolute;
    top: 110px; left: 0; right: 0;
    display: flex; align-items: center; justify-content: center; gap: 10px;
  }
  .brand-dot {
    width: 22px; height: 22px; border-radius: 50%;
    background: var(--accent-blue);
  }
  .front-brand .brand-name {
    font-family: "Poppins", sans-serif;
    font-weight: 700; font-size: 28px;
    color: var(--accent-blue);
  }
  .contact-block {
    position: absolute;
    left: 46px; bottom: 60px;
  }
  .holder-name {
    font-family: "Arimo", sans-serif;
    font-weight: 700; font-size: 30px;
    color: var(--accent-blue); line-height: 1.05;
  }
  .holder-role {
    font-size: 17px; color: #555; margin-top: 2px;
  }
  .divider {
    width: 78px; height: 1px; background: var(--rule);
    margin: 26px 0 22px;
  }
  .address, .channels { font-size: 17px; color: var(--ink); line-height: 1.35; }
  .channels .label { color: var(--accent-blue); font-weight: 700; margin-right: 6px; }

  /* Back: landscape */
  .card-back {
    left: 490px; top: 345px;
    width: 630px; height: 360px;
    background: var(--brand-blue);
    border: 2px solid #e8f1f8;
  }
  .back-lockup {
    position: absolute; inset: 0;
    display: flex; flex-direction: column; align-items: center; justify-content: center;
  }
  .back-brand {
    display: flex; align-items: center; gap: 16px;
  }
  .back-brand .brand-dot { width: 34px; height: 34px; background: var(--white); }
  .back-brand .brand-name {
    font-family: "Poppins", sans-serif;
    font-weight: 700; font-size: 64px; color: var(--white);
    line-height: 1;
  }
  .tagline {
    font-family: "Poppins", sans-serif;
    font-weight: 500; font-size: 18px; color: var(--white);
    margin-top: 12px; letter-spacing: 0.2px;
  }
</style>
</head>
<body>
  <section class="card card-front">
    <div class="front-brand">
      <span class="brand-dot"></span>
      <span class="brand-name">Veltrano.co</span>
    </div>
    <div class="contact-block">
      <p class="holder-name">Marcus Hale</p>
      <p class="holder-role">President</p>
      <div class="divider"></div>
      <p class="address">2716 Harbor Lane<br>Glen Cove, NY 11542</p>
      <div class="divider"></div>
      <p class="channels">
        <span class="label">P :</span>(555) 0142-7781<br>
        <span class="label">E :</span>name@veltrano.com<br>
        <span class="label">W :</span>www.veltrano.com
      </p>
    </div>
  </section>

  <section class="card card-back">
    <div class="back-lockup">
      <div class="back-brand">
        <span class="brand-dot"></span>
        <span class="brand-name">Veltrano.co</span>
      </div>
      <p class="tagline">Polar Expeditions Specialists</p>
    </div>
  </section>
</body>
</html>
```